SOLVE Study flyer

I need help designing a flyer for a research study that will include brain imaging in adolescents. The info is in the attached document. The study is called the Sequoia Outlook Lantern Valley Echo (SOLVE) study. Ideally this would be returned as a document that I can edit in the future as we will have several new recruitment phases (different age groups, etc. I also would love to have a logo designed as part of this project, but I recognize that might be a separate design request.

```html
<!DOCTYPE html>
<html lang="en">
<head>
<meta charset="utf-8">
<title>SOLVE Study Flyer</title>
<link href="https://fonts.googleapis.com/css2?family=Anton&family=Poppins:wght@400;500;600;700&display=swap" rel="stylesheet">
<style>
  :root{
    --purple:#56357f;
    --teal:#0b8c89;
    --teal-light:#4fbfb9;
    --aqua-bg:#ddf9fa;
    --navy:#0b1946;
    --ink:#111111;
    --white:#ffffff;
  }
  *{margin:0;padding:0;box-sizing:border-box}
  html,body{width:927px;height:1200px;overflow:hidden;background:var(--white)}
  body{font-family:'Poppins',sans-serif;color:var(--ink)}
  .flyer{position:relative;width:927px;height:1200px;overflow:hidden;background:var(--white)}
  .abs{position:absolute}

  .hero-art{left:452px;top:0;width:475px;height:453px}
  .study-mark{left:46px;top:14px;font-family:'Anton',sans-serif;font-size:92px;line-height:1;color:var(--purple);letter-spacing:1px}
  .study-title{left:48px;top:124px;width:400px;font-weight:600;font-size:20px;line-height:32px;color:var(--ink);text-transform:uppercase;letter-spacing:.3px}
  .divider{left:47px;top:229px}

  .question{left:46px;display:flex;gap:14px;align-items:flex-start}
  .question p{font-weight:600;font-size:23px;line-height:31px;width:330px}
  .question .hl-teal{color:var(--teal)}
  .question .hl-purple{color:var(--purple)}

  .band{left:0;top:453px;width:927px;height:154px;background:var(--purple);border-radius:77px 0 0 77px}
  .band-icon{left:22px;top:474px}
  .band-text{left:167px;top:484px;width:660px;color:var(--white);font-weight:600;font-size:18.2px;line-height:32px}
  .band-text .hl{color:var(--teal-light)}

  .section-head{font-weight:700;font-size:21px;line-height:29px;text-transform:uppercase}
  .involves-head{left:133px;top:643px;color:var(--purple)}
  .step{left:53px;display:flex;gap:14px}
  .step h3{font-weight:700;font-size:17.5px;line-height:29px}
  .step p{font-size:14.6px;line-height:22.5px;width:310px}

  .eligibility{left:484px;top:637px;width:396px;height:397px;background:var(--aqua-bg);border-radius:10px}
  .eligibility-head{left:589px;top:672px;color:var(--teal)}
  .criterion{left:512px;display:flex;gap:16px;align-items:flex-start;font-size:17px;line-height:29px;width:350px}
  .rule{left:484px;width:396px;height:1px;background:#b7dfe0}

  .footer{left:0;top:1064px;width:927px;height:136px;background:var(--navy)}
  .pay-tab{left:195px;top:1064px;width:537px;height:45px;background:var(--teal);border-radius:0 0 28px 28px;color:var(--white);font-weight:700;font-size:19px;text-align:center;line-height:47px}
  .pay-tab strong{font-size:30px;vertical-align:-2px}
  .cta{left:0;top:1124px;width:927px;text-align:center;color:var(--white);font-weight:700;font-size:18.5px;letter-spacing:.3px;text-transform:uppercase}
  .contact{left:0;top:1160px;width:927px;display:flex;justify-content:center;align-items:center;gap:12px;color:var(--white);font-weight:600;font-size:20px}
  .form-code{right:10px;top:1180px;color:var(--white);font-weight:600;font-size:9px}
</style>
</head>
<body>
<main class="flyer">

  <svg class="abs hero-art" viewBox="452 0 475 453" width="475" height="453">
    <defs>
      <radialGradient id="photoTone" cx="0.55" cy="0.45" r="0.7">
        <stop offset="0" stop-color="#e7b7a3"/>
        <stop offset="0.55" stop-color="#9a6a58"/>
        <stop offset="1" stop-color="#3e2f2a"/>
      </radialGradient>
      <radialGradient id="brainTone" cx="0.5" cy="0.5" r="0.6">
        <stop offset="0" stop-color="#7a5ce0"/>
        <stop offset="1" stop-color="#1a1238"/>
      </radialGradient>
      <clipPath id="bandClip"><rect x="452" y="0" width="475" height="453"/></clipPath>
    </defs>
    <g clip-path="url(#bandClip)">
      <circle cx="712" cy="212" r="258" fill="var(--purple)"/>
      <circle cx="712" cy="232" r="252" fill="var(--teal)"/>
      <rect x="452" y="0" width="10" height="453" fill="#fff"/>
      <circle cx="725" cy="215" r="250" fill="#fff"/>
      <circle cx="730" cy="216" r="244" fill="url(#photoTone)" role="img" aria-label="Photo of a teenage girl in a pink sweater holding a book"/>
      <circle cx="850" cy="80" r="90" fill="#fff"/>
      <circle cx="850" cy="80" r="87" fill="url(#brainTone)" role="img" aria-label="Illustration of a glowing digital brain"/>
    </g>
  </svg>

  <div class="abs study-mark">SOLVE</div>
  <h1 class="abs study-title">Sequoia Outlook Lantern Valley Echo (SOLVE) Study.</h1>
  <svg class="abs divider" width="152" height="22" viewBox="0 0 152 22">
    <line x1="1" y1="11" x2="133" y2="11" stroke="var(--teal)" stroke-width="4"/>
    <circle cx="142" cy="11" r="8" fill="#fff" stroke="var(--purple)" stroke-width="3"/>
  </svg>

  <div class="abs question" style="top:268px">
    <svg width="30" height="30" viewBox="0 0 30 30"><circle cx="14" cy="16" r="11.5" fill="none" stroke="var(--teal)" stroke-width="3"/><path d="M8 15l5 5L27 5" fill="none" stroke="var(--teal)" stroke-width="3" stroke-linecap="round"/></svg>
    <p>Are you the parent of a child age <span class="hl-teal">10-17?</span></p>
  </div>
  <div class="abs question" style="top:348px">
    <svg width="30" height="30" viewBox="0 0 30 30"><circle cx="14" cy="16" r="11.5" fill="none" stroke="var(--teal)" stroke-width="3"/><path d="M8 15l5 5L27 5" fill="none" stroke="var(--teal)" stroke-width="3" stroke-linecap="round"/></svg>
    <p>Do they <span class="hl-purple">worry or overthink</span> negative emotions?</p>
  </div>

  <div class="abs band"></div>
  <svg class="abs band-icon" width="114" height="114" viewBox="0 0 114 114" role="img" aria-label="Brain icon">
    <circle cx="57" cy="57" r="55" fill="none" stroke="var(--teal)" stroke-width="3"/>
    <path d="M40 40c4-9 16-11 22-5 8-4 18 1 18 10 7 3 7 14 0 17 1 9-9 14-16 10l-4 12-4-10c-8 2-16-2-17-9-8-2-10-13-3-17 0-4 2-7 4-8z" fill="none" stroke="var(--teal)" stroke-width="2.5" stroke-linejoin="round"/>
  </svg>
  <p class="abs band-text">Lantern Valley University researchers are seeking <span class="hl">girls age 10-17</span> for a study about brain activity in emotions and decision-making and how they relate to puberty, anxiety and depression.</p>

  <svg class="abs" style="left:49px;top:636px" width="70" height="70" viewBox="0 0 70 70">
    <circle cx="35" cy="35" r="34" fill="var(--purple)"/>
    <rect x="18" y="18" width="22" height="26" rx="2" fill="none" stroke="#fff" stroke-width="2"/>
    <path d="M22 25h10M22 31h10M22 37h8" stroke="#fff" stroke-width="2"/>
    <circle cx="41" cy="35" r="7" fill="var(--purple)" stroke="#fff" stroke-width="2"/>
    <path d="M46 40l6 7" stroke="#fff" stroke-width="3" stroke-linecap="round"/>
    <path d="M17 54h22" stroke="#fff" stroke-width="3"/>
  </svg>
  <h2 class="abs section-head involves-head">Study Participation<br>Involves:</h2>

  <div class="abs step" style="top:731px">
    <svg width="64" height="64" viewBox="0 0 64 64"><circle cx="32" cy="32" r="31" fill="var(--teal)"/><rect x="16" y="17" width="14" height="10" rx="2" fill="#fff"/><circle cx="42" cy="22" r="4" fill="#fff"/><path d="M35 34h14v12H35z" fill="#fff"/><circle cx="24" cy="36" r="4" fill="#fff"/><path d="M16 48c0-6 4-8 8-8s8 2 8 8z" fill="#fff"/></svg>
    <div>
      <h3>One one-hour interview<br>(online or in-person)</h3>
      <p>Where your child will discuss their thoughts</p>
    </div>
  </div>

  <div class="abs step" style="top:835px">
    <svg width="64" height="64" viewBox="0 0 64 64"><circle cx="32" cy="32" r="31" fill="var(--navy)"/><rect x="17" y="16" width="30" height="24" rx="2" fill="none" stroke="#fff" stroke-width="2.5"/><path d="M23 23h18M23 29h18M23 35h10" stroke="#fff" stroke-width="2"/><path d="M26 46h12" stroke="#fff" stroke-width="2.5"/></svg>
    <div>
      <h3>Online questionnaires</h3>
      <p>(parent and child)</p>
    </div>
  </div>

  <div class="abs step" style="top:917px">
    <svg width="64" height="64" viewBox="0 0 64 64"><circle cx="32" cy="32" r="31" fill="var(--teal-light)"/><circle cx="32" cy="33" r="17" fill="none" stroke="#fff" stroke-width="3" stroke-dasharray="80 8"/><text x="32" y="39" text-anchor="middle" font-family="Poppins,sans-serif" font-weight="700" font-size="15" fill="#fff">24</text></svg>
    <div>
      <h3>One two-hour</h3>
      <p>Visit where your child will complete an MRI scan, answer questions about their puberty stage, and have a small hair sample taken to study puberty hormones</p>
    </div>
  </div>

  <div class="abs eligibility"></div>
  <svg class="abs" style="left:511px;top:667px" width="64" height="64" viewBox="0 0 64 64">
    <circle cx="32" cy="32" r="30.5" fill="#fff" stroke="var(--teal-light)" stroke-width="2"/>
    <circle cx="22" cy="27" r="4" fill="var(--teal)"/><circle cx="42" cy="27" r="4" fill="var(--teal)"/><circle cx="32" cy="25" r="5" fill="var(--teal)"/>
    <path d="M15 40c0-6 3-8 7-8s6 2 6 4M49 40c0-6-3-8-7-8s-6 2-6 4" fill="var(--teal)"/>
    <path d="M23 44c0-7 4-10 9-10s9 3 9 10z" fill="var(--teal)"/>
  </svg>
  <h2 class="abs section-head eligibility-head">Your child may be<br>eligible if they:</h2>

  <div class="abs criterion" style="top:760px">
    <svg width="30" height="30" viewBox="0 0 30 30"><circle cx="14" cy="16" r="12" fill="none" stroke="var(--teal)" stroke-width="2.5"/><path d="M8 15l5 5L27 5" fill="none" stroke="var(--teal)" stroke-width="2.5" stroke-linecap="round"/></svg>
    <span>Are age 10-17</span>
  </div>
  <div class="abs rule" style="top:803px"></div>
  <div class="abs criterion" style="top:818px">
    <svg width="30" height="30" viewBox="0 0 30 30" style="margin-top:10px"><circle cx="14" cy="16" r="12" fill="none" stroke="var(--teal)" stroke-width="2.5"/><path d="M8 15l5 5L27 5" fill="none" stroke="var(--teal)" stroke-width="2.5" stroke-linecap="round"/></svg>
    <span>Tend to worry or overthink negative thoughts</span>
  </div>
  <div class="abs rule" style="top:892px"></div>
  <div class="abs criterion" style="top:905px">
    <svg width="30" height="30" viewBox="0 0 30 30" style="margin-top:12px"><circle cx="14" cy="16" r="12" fill="none" stroke="var(--teal)" stroke-width="2.5"/><path d="M8 15l5 5L27 5" fill="none" stroke="var(--teal)" stroke-width="2.5" stroke-linecap="round"/></svg>
    <span>Have not been diagnosed with psychosis, learning problems, or autism</span>
  </div>

  <div class="abs footer"></div>
  <div class="abs pay-tab">Compensation up to <strong>$140</strong></div>
  <p class="abs cta">Interested in participating? Want more information? Please contact us!</p>
  <div class="abs contact">
    <svg width="38" height="26" viewBox="0 0 38 26"><rect x="1" y="1" width="36" height="24" fill="var(--teal)"/><path d="M1 1l18 14L37 1M1 25l13-12M37 25L24 13" fill="none" stroke="var(--navy)" stroke-width="2"/></svg>
    <span>solvestudy@lanternhealth.org</span>
  </div>
  <div class="abs form-code">C56</div>
</main>
</body>
</html>
```